Marlowe Group needs a business card

I would like the card to be simple but modern and elegant.
I like black and white.
or black and gold.
we are a private finance lender and also are involved in property and property developments.

please look at the business card photos i provided i would like M.G only one one side and all the other details on the other side use fonts that tie in with my theme.

Industry/Entity Type

Finance

Contact Information for Business Card

Marlowe Group (M.G) Daniel Marlowe M: 0413586207 E: danmarl@inboxmail.test

Font styles to use
Other font styles liked:
• Use fonts that would reflect our business

Colors
000000
ffffff

Requirements
Must have
• one side of details
• other side has either M.G or Marlowe Group like in the photos provided

```html
<!DOCTYPE html>
<html lang="en">
<head>
<meta charset="utf-8">
<title>Marlowe Group – Business Card</title>
<link href="https://fonts.googleapis.com/css2?family=Work+Sans:wght@400;500&display=swap" rel="stylesheet">
<style>
  :root {
    --backdrop: #e6e4df;
    --card: #1f1f1f;
    --ink: #ffffff;
    --ink-soft: #d9d9d9;
    --rule: #cfcfcf;
  }
  * { margin: 0; padding: 0; box-sizing: border-box; }
  html, body {
    width: 1200px;
    height: 900px;
    overflow: hidden;
    background: var(--backdrop);
    font-family: "Work Sans", Arial, sans-serif;
  }
  .canvas {
    width: 1200px;
    height: 900px;
    display: flex;
    flex-direction: column;
    align-items: center;
    justify-content: center;
    gap: 48px;
  }
  .card {
    width: 630px;
    height: 360px;
    background: var(--card);
    color: var(--ink);
    position: relative;
    box-shadow: 0 8px 22px rgba(0,0,0,0.18);
  }
  .card--front .company-name {
    position: absolute;
    left: 150px;
    top: 150px;
    font-size: 34px;
    font-weight: 500;
    letter-spacing: 0.5px;
  }
  .card--back .details {
    position: absolute;
    left: 170px;
    top: 110px;
    width: 290px;
  }
  .details .person-name {
    font-size: 22px;
    font-weight: 500;
    letter-spacing: 1px;
    text-transform: uppercase;
    text-align: right;
    padding-right: 6px;
  }
  .details .divider {
    display: block;
    margin: 10px 0 14px;
  }
  .details .contact {
    font-size: 18px;
    color: var(--ink-soft);
    line-height: 1.5;
    letter-spacing: 0.4px;
  }
  .details .contact .phone { padding-left: 26px; }
</style>
</head>
<body>
  <main class="canvas">
    <section class="card card--front" aria-label="Card front">
      <h1 class="company-name">Marlowe Group</h1>
    </section>
    <section class="card card--back" aria-label="Card back">
      <div class="details">
        <p class="person-name">Daniel Marlowe</p>
        <svg class="divider" width="290" height="2" viewBox="0 0 290 2" aria-hidden="true">
          <line x1="0" y1="1" x2="290" y2="1" stroke="var(--rule)" stroke-width="1.5"/>
        </svg>
        <div class="contact">
          <p class="phone">M: 0413586207</p>
          <p class="email">E: danmarl@inboxmail.test</p>
        </div>
      </div>
    </section>
  </main>
</body>
</html>
```